Business Card Design Project - Sports Brand

Brisk is a e-commerce fitness wear brand for ladies who are into gym, pole and swim.

Card should not be overly cluttered and should include the following:

1. logo
2. Name of the company (Use "Brisk Loom Pte Ltd" for now)
3. Address of company (Use a mock address)
4. Representative's name and contact info etc. (use a mock name and contact info)
5. website address

Target Market(s)

Women who are into pole , gym, and swim.

Women who shop online

Industry/Entity Type

E-Commerce

Colors

Designer to choose colors to be used in the design.

Requirements
Nice to have
• feminine sublimation of colours

Need not be printed on traditional paper. We would like the design to be revolutionary and interesting to the eye :)
Should not have
• the design should not be traditional looking. Do not include illustrations of Bikinis, yoga poses etc. in the card.

```html
<!DOCTYPE html>
<html lang="en">
<head>
<meta charset="utf-8">
<title>Brisk Loom – Business Card</title>
<link href="https://fonts.googleapis.com/css2?family=Libre+Baskerville:wght@400;700&display=swap" rel="stylesheet">
<style>
  :root {
    --stage: #1f1f21;
    --card: #ffffff;
    --pink: #e2457f;
    --wine: #b3243a;
    --grey: #666569;
    --wash-pink: #e05a9e;
    --wash-rose: #ea4f6b;
    --wash-orange: #f05a28;
  }
  * { margin: 0; padding: 0; box-sizing: border-box; }
  html, body { width: 1200px; height: 900px; overflow: hidden; }
  body {
    background: var(--stage);
    font-family: "Libre Baskerville", Georgia, serif;
    position: relative;
  }
  .card {
    position: absolute;
    top: 170px;
    width: 360px;
    height: 560px;
    background: var(--card);
    border-radius: 14px;
  }
  .card--front { left: 210px; }
  .card--back { left: 630px; }

  .front-mark {
    position: absolute;
    left: 40px; top: 120px;
    width: 280px; height: 280px;
    border-radius: 50%;
    background: radial-gradient(circle at 55% 68%, var(--wash-orange) 0%, var(--wash-rose) 45%, var(--wash-pink) 100%);
    display: flex; align-items: center; justify-content: center;
  }
  .front-mark__name {
    color: #ffffff;
    font-size: 54px;
    font-weight: 400;
  }

  .brand {
    position: absolute;
    left: 34px; top: 44px;
    display: flex; align-items: center; gap: 14px;
  }
  .brand__wash {
    width: 150px; height: 150px;
    border-radius: 50%;
    background: radial-gradient(circle at 55% 70%, var(--wash-orange) 0%, var(--wash-rose) 45%, var(--wash-pink) 100%);
  }
  .brand__name {
    color: var(--wine);
    font-size: 46px;
    font-weight: 400;
    line-height: 1;
  }
  .brand__tagline {
    position: absolute;
    left: 200px; top: 204px;
    color: var(--grey);
    font-size: 13px;
    letter-spacing: 0.5px;
  }

  .contact {
    position: absolute;
    left: 0; right: 0; top: 262px;
    text-align: center;
  }
  .contact__name {
    color: var(--pink);
    font-size: 19px;
    letter-spacing: 1.5px;
    text-transform: uppercase;
  }
  .contact__role {
    color: var(--grey);
    font-size: 14px;
    margin-top: 2px;
  }
  .contact__list {
    list-style: none;
    margin-top: 26px;
    color: var(--grey);
    font-size: 15px;
    line-height: 1.5;
  }
  .contact__label { color: var(--pink); margin-right: 6px; }
  .company {
    margin-top: 22px;
    color: var(--grey);
    font-size: 14px;
    line-height: 1.4;
  }
  .company__name {
    color: var(--pink);
    text-transform: uppercase;
    letter-spacing: 1px;
    font-size: 15px;
  }
</style>
</head>
<body>
  <section class="card card--front">
    <div class="front-mark" role="img" aria-label="Soft pink to orange watercolour wash behind the brand name">
      <span class="front-mark__name">Brisk</span>
    </div>
  </section>

  <section class="card card--back">
    <div class="brand">
      <div class="brand__wash" role="img" aria-label="Soft pink to orange watercolour wash"></div>
      <span class="brand__name">Brisk</span>
    </div>
    <p class="brand__tagline">Yoga · Swim · Pole</p>

    <div class="contact">
      <h1 class="contact__name">Maren Tully</h1>
      <p class="contact__role">Director</p>
      <ul class="contact__list">
        <li><span class="contact__label">P:</span>555 014 2297</li>
        <li><span class="contact__label">E:</span>maren@briskloom.com</li>
        <li><span class="contact__label">W:</span>www.briskloom.com</li>
      </ul>
      <div class="company">
        <p class="company__name">Brisk Loom Pte Ltd</p>
        <p>Unit 58, Corvel Lane,</p>
        <p>Singapore 408812</p>
      </div>
    </div>
  </section>
</body>
</html>
```